KAJU Freightways #ALLKAJU Business Cards & Letterhead

I am looking to business cards designed for our organization. We are currently undergoing a small re-branding that is taking place. Our organization is called KAJU Freightways and we are headquartered in Phoenix, AZ. We primarily provide transportation and logistics services to the Marlow Parcel Bureau who is our largest customer. I would like to see a design that incorporates name, title, contact info, website, and address (this will be different depending on the employee). I would also like to see some color on the business card using our logo colors or a variation. I would like our logo on the back of the business card with the website displayed. The final design should communicate that we are a next generation transportation operate that focuses on being driver-first, customer-centric, innovative, and sustainable.We would also like our #ALLKAJU catch phrase incorporated as well.

Target Market(s)

Transportation & Logistics

Industry/Entity Type

Trucking Company

Contact Information for Business Card

-First and Last Name
-Position Title
-Contact Phone
-Contact Email
-Physical Address

Font styles to use
Serif

Colors

Designer to choose colors to be used in the design.

Requirements
Must have
• -KAJU logo prominently displayed
• -#ALLKAJU catch phrase used
• -Some amount of color, design gradient, etc.
• -Logo on the back with website listed (https://www.kajufreightco.example)

```html
<!DOCTYPE html>
<html lang="en">
<head>
<meta charset="utf-8">
<title>KAJU Freightways Business Card</title>
<link rel="stylesheet" href="https://fonts.googleapis.com/css2?family=Lora:ital,wght@0,400;0,600;0,700&display=swap">
<style>
  :root {
    --bg: #a9a9ab;
    --teal-dark: #013840;
    --teal: #04505a;
    --green: #7cc242;
    --pattern-green: #2f6b43;
    --silver: #d3d6d9;
    --ink-grey: #6d6e71;
    --rule: #9a9a9a;
    --white: #ffffff;
  }
  * { margin: 0; padding: 0; box-sizing: border-box; }
  html, body { width: 1200px; height: 960px; overflow: hidden; }
  body {
    background: var(--bg);
    font-family: "Lora", Georgia, serif;
    position: relative;
  }
  .card {
    position: absolute;
    width: 700px;
    height: 400px;
    overflow: hidden;
  }

  /* Back of card */
  .card-back {
    left: 60px;
    top: 60px;
    background: linear-gradient(135deg, var(--teal-dark), var(--teal));
  }
  .card-back .pattern {
    position: absolute;
    inset: 0;
    background:
      radial-gradient(circle at 20% 30%, rgba(47,107,67,0.35), transparent 30%),
      radial-gradient(circle at 80% 25%, rgba(47,107,67,0.35), transparent 30%),
      radial-gradient(circle at 30% 85%, rgba(47,107,67,0.3), transparent 30%),
      radial-gradient(circle at 78% 80%, rgba(47,107,67,0.3), transparent 30%);
  }
  .card-back .back-stack {
    position: absolute;
    left: 0;
    right: 0;
    top: 118px;
    display: flex;
    flex-direction: column;
    align-items: center;
    gap: 14px;
  }
  .card-back .wordmark {
    display: flex;
    align-items: center;
    gap: 14px;
  }
  .card-back .wordmark-dot {
    width: 26px;
    height: 26px;
    border-radius: 50%;
    border: 3px solid var(--silver);
  }
  .card-back .wordmark-name {
    font-weight: 700;
    font-size: 68px;
    line-height: 1;
    letter-spacing: 2px;
    color: var(--silver);
  }
  .card-back .tagline {
    font-weight: 600;
    font-size: 18px;
    letter-spacing: 3px;
    color: var(--green);
  }
  .card-back .back-site {
    font-size: 15px;
    letter-spacing: 0.5px;
    color: var(--silver);
  }

  /* Front of card */
  .card-front {
    left: 440px;
    top: 500px;
    background: var(--white);
  }
  .logo {
    position: absolute;
    right: 48px;
    top: 40px;
    display: flex;
    align-items: center;
    gap: 10px;
  }
  .logo-dot {
    width: 22px;
    height: 22px;
    border-radius: 50%;
    border: 3px solid var(--green);
  }
  .logo-name {
    font-weight: 700;
    font-size: 40px;
    line-height: 1;
    color: var(--teal);
    letter-spacing: 1px;
  }
  .person-name {
    position: absolute;
    left: 48px;
    top: 206px;
    font-weight: 700;
    font-size: 22px;
    line-height: 28px;
    color: var(--teal);
    letter-spacing: 0.5px;
  }
  .divider {
    position: absolute;
    left: 48px;
    right: 48px;
    top: 240px;
    height: 1px;
    background: var(--rule);
  }
  .person-title {
    position: absolute;
    left: 48px;
    top: 246px;
    font-size: 17px;
    line-height: 24px;
    color: var(--green);
  }
  .address {
    position: absolute;
    right: 48px;
    top: 252px;
    text-align: right;
    font-style: normal;
    font-size: 14px;
    line-height: 19px;
    color: var(--ink-grey);
  }
  .contacts {
    position: absolute;
    left: 48px;
    top: 284px;
    list-style: none;
    font-size: 14px;
    line-height: 21px;
    color: var(--ink-grey);
  }
  .contacts li { display: flex; align-items: center; gap: 10px; }
  .contacts svg { width: 12px; height: 12px; fill: var(--teal-dark); flex: none; }
  .band-teal {
    position: absolute;
    left: 0;
    bottom: 0;
    width: 510px;
    height: 12px;
    background: var(--teal);
  }
  .band-green {
    position: absolute;
    left: 510px;
    right: 0;
    bottom: 12px;
    height: 8px;
    background: var(--green);
  }
</style>
</head>
<body>
  <section class="card card-back">
    <div class="pattern" role="img" aria-label="Faint repeated brand circle pattern on dark teal"></div>
    <div class="back-stack">
      <div class="wordmark">
        <span class="wordmark-dot"></span>
        <span class="wordmark-name">KAJU</span>
      </div>
      <p class="tagline">#ALLKAJU</p>
      <p class="back-site">https://www.kajufreightco.example</p>
    </div>
  </section>

  <section class="card card-front">
    <div class="logo">
      <span class="logo-dot"></span>
      <span class="logo-name">KAJU</span>
    </div>

    <h1 class="person-name">DANA WHITLOCK</h1>
    <div class="divider"></div>
    <p class="person-title">President</p>

    <address class="address">2210 Saguaro<br>Way Phoenix<br>Arizona 85004</address>

    <ul class="contacts">
      <li>
        <svg viewBox="0 0 24 24" aria-hidden="true"><path d="M6.6 10.8a15 15 0 0 0 6.6 6.6l2.2-2.2a1 1 0 0 1 1-.25 11.4 11.4 0 0 0 3.6.57 1 1 0 0 1 1 1V20a1 1 0 0 1-1 1A17 17 0 0 1 3 4a1 1 0 0 1 1-1h3.5a1 1 0 0 1 1 1c0 1.25.2 2.45.57 3.6a1 1 0 0 1-.25 1z"/></svg>
        480-555-0142
      </li>
      <li>
        <svg viewBox="0 0 24 24" aria-hidden="true"><path d="M2 5h20v14H2zm2 2v.5l8 5 8-5V7l-8 5z"/></svg>
        dana@kajufreightco.example
      </li>
      <li>
        <svg viewBox="0 0 24 24" aria-hidden="true"><circle cx="12" cy="12" r="10"/></svg>
        www.kajufreightco.example
      </li>
    </ul>

    <div class="band-teal"></div>
    <div class="band-green"></div>
  </section>
</body>
</html>
```